Logo and Card design for KRV Home Solutions LLC

I need an edgier logo and business card designs. Current logo attached. I like the colors below. I would like the logo to incorporate a home in the design.
Title = Principal-Acquisitions
Email:KRVHOMESOLUTIONS@fernmail.example
555-214-0937
facebook
IG
2 sided business card with the front being contact info a slogan about selling a home fast. The back incorporating What we do. Buy houses, land, or commercial property as is. We find solutions to make the process of selling simple and fair.

Target Market(s)

Motivated house sellers.

Industry/Entity Type

Business

Contact Information for Business Card

Who we are: We are a Faith based Real Estate Investment Company. We pay cash for homes in any condition and can close quick. Whatever the reason you need to sell fast, we can help. We believe in creating win-win solutions to help you in your time of need. We care! We can help!

Logo Text

KRV Home Solutions LLC

Font styles to use
Sans Serif

Colors
33a6d7
0355a3
85abd2
cee9f5
9d9d9d
b2b2b2
ffffff

Requirements
Must have
• Old logo attached. I want something edgier.
• Company name, phone number, description on the back of what we can do. Pay all cash. Buy in as is condition. No fees,Commisions or closing costs.Close quick. No hassles with solutions to meet your unique situation.
• Call today for an offer within 24 hours.

```html
<!DOCTYPE html>
<html lang="en">
<head>
<meta charset="UTF-8">
<title>KRV Home Solutions – Business Card</title>
<link rel="stylesheet" href="https://fonts.googleapis.com/css2?family=Lato:wght@400;700&display=swap">
<style>
  :root {
    --page-bg: #e9e7e4;
    --card-navy: #1f3a6e;
    --card-gray: #666666;
    --text-white: #ffffff;
    --seal-white: #f2f2f2;
    --seal-ink: #1f3a6e;
  }
  * { box-sizing: border-box; margin: 0; padding: 0; }
  html, body {
    width: 1200px; height: 900px; overflow: hidden;
    background: var(--page-bg);
    font-family: "Lato", sans-serif;
  }
  .business-card {
    position: absolute; left: 160px; top: 178px;
    width: 880px; height: 544px;
    background: var(--card-gray);
    box-shadow: 0 10px 30px rgba(0,0,0,0.18);
    overflow: hidden;
  }
  .navy-panel {
    position: absolute; left: 0; top: 0;
    width: 630px; height: 100%;
    background: var(--card-navy);
  }
  .contact-block {
    position: absolute; left: 39px; top: 52px;
    color: var(--text-white);
  }
  .person-name {
    font-weight: 700; font-size: 31px; letter-spacing: 0.3px; line-height: 1.1;
  }
  .person-title { font-size: 23px; line-height: 1.3; margin-bottom: 20px; }
  .contact-line {
    display: flex; align-items: center; gap: 8px;
    font-size: 24px; line-height: 1.35; white-space: nowrap;
  }
  .contact-line.email { font-size: 21px; }
  .contact-line svg { width: 19px; height: 19px; flex: none; }
  .services-list {
    position: absolute; left: 39px; top: 283px;
    list-style: none; color: var(--text-white);
    font-size: 21px; line-height: 28px;
  }
  .services-list li { position: relative; padding-left: 15px; }
  .services-list li::before {
    content: ""; position: absolute; left: 0; top: 10px;
    width: 9px; height: 9px; border-radius: 50%; background: var(--text-white);
  }
  .brand-seal {
    position: absolute; left: 432px; top: 74px;
    width: 396px; height: 396px; border-radius: 50%;
    background: radial-gradient(circle at 40% 35%, #ffffff, var(--seal-white) 60%, #dcdcdc);
    display: flex; align-items: center; justify-content: center;
    text-align: center;
  }
  .brand-name {
    font-weight: 700; font-size: 40px; line-height: 1.1;
    color: var(--seal-ink);
  }
</style>
</head>
<body>
  <div class="business-card">
    <div class="navy-panel">
      <div class="contact-block">
        <h1 class="person-name">MARCUS HALE</h1>
        <p class="person-title">Principal-Acquisitions</p>
        <p class="contact-line">
          <svg viewBox="0 0 20 20" aria-hidden="true"><path fill="#fff" d="M2 6c0-2 2-3 4-3h8c2 0 4 1 4 3v1h-4V5H6v2H2z M5 9h10l2 7H3z M8 11a2 2 0 1 0 4 0a2 2 0 1 0-4 0"/></svg>
          555-214-0937
        </p>
        <p class="contact-line email">
          <svg viewBox="0 0 20 20" aria-hidden="true"><rect x="2" y="4" width="16" height="12" fill="#fff"/><path d="M2 4l8 7l8-7" fill="none" stroke="#1f3a6e" stroke-width="1.6"/></svg>
          krvhomesolutions@fernmail.example
        </p>
      </div>
      <ul class="services-list">
        <li>Buy houses, land or commercial<br>property as is.</li>
        <li>Pay all cash.</li>
        <li>Buy in as is condition.</li>
        <li>No fees, commisions or closing costs.</li>
        <li>Close quick. No hassles with<br>solutions to meet your unique situation.</li>
        <li>Call today for an offer within 24 hours</li>
      </ul>
    </div>
    <div class="brand-seal">
      <p class="brand-name">KRV Home<br>Solutions LLC</p>
    </div>
  </div>
</body>
</html>
```